Introduction flyer

Brightpath Dietetics & Vitality Advisory, is a new holistic nutritional therapy specialising in womens health. I want a flyer that appeals to women between 15 to 60. It must speak "health, food & balance". I have attached the basic info I need included in the text. I like Greens & Blues, soft text. My flyer will be distributed to cafes, shops, fitness centres, hung up in grocery stores & health centres etc. The QELR & HPVA logos need to appear on the flyer to show I am fully registered. My own logo & company name is attached.

Target Market(s)

Women from 10 to 60 years old.

Industry/Entity Type

Nutritionist

Colors
32a6d7
abd037
33b8a4
fbf289
ffcf3e
b768aa
d5d5d5
dcdcdc
e8e8e8

Requirements
Must have
• An image of healthy food & ladies. A group of women eating soup, stews or curry type dishes, with plenty of colour - no bread or white wine, and not just fruit please. Food that looks enjoyable to the average person.
• Nutrition is main part of my job, so please keep that in mind & emphasise food & natural well being.
Should not have
• People exercising, men, white wine, bread, cakes, sweets etc..

```html
<!DOCTYPE html>
<html lang="en">
<head>
<meta charset="utf-8">
<title>Brightpath Dietetics &amp; Vitality Advisory – Introduction Flyer</title>
<link href="https://fonts.googleapis.com/css2?family=Open+Sans:wght@400;600;700&family=Roboto+Condensed:wght@700&display=swap" rel="stylesheet">
<style>
  :root {
    --page-bg: #eeeeec;
    --ink: #3a3a3a;
    --blue: #2b6cb3;
    --green: #1f8a3e;
    --band-blue: #3b78bf;
    --teal: #2a9fb6;
    --dark: #28312e;
    --column-green: #1f9645;
    --email-blue: #3f8fd1;
    --light-grey: #eeeeee;
    --white: #ffffff;
  }
  * { box-sizing: border-box; margin: 0; padding: 0; }
  html, body { width: 1020px; height: 1200px; overflow: hidden; background: var(--page-bg); }
  .canvas { position: relative; width: 1020px; height: 1200px; overflow: hidden; }
  .flyer {
    position: absolute; left: 99px; top: 19px;
    width: 596px; height: 842px;
    transform: scale(1.38); transform-origin: 0 0;
    background: var(--white);
    font-family: "Open Sans", sans-serif; color: var(--ink);
    box-shadow: 0 2px 6px rgba(0,0,0,.18);
    overflow: hidden;
  }
  .photo { position: absolute; }
  .photo--fruit { left: 0; top: 0; width: 372px; height: 292px;
    background: radial-gradient(ellipse at 45% 60%, #a6b83c 0%, #c8542c 30%, #6a4a24 60%, #141414 85%); }
  .photo--desserts { left: 378px; top: 0; width: 218px; height: 186px;
    background: linear-gradient(160deg, #9c8f86 0%, #f4efe6 45%, #e7d9bd 70%, #c9364a 100%); }
  .photo--berries { left: 378px; top: 192px; width: 106px; height: 100px;
    background: radial-gradient(circle at 50% 60%, #7c3040 0%, #d8d8d8 55%, #f2f2f2 100%); }
  .photo--vegetables { left: 490px; top: 192px; width: 106px; height: 100px;
    background: linear-gradient(135deg, #f3f3f0 0%, #d97a25 40%, #3d8a30 70%, #c53a28 100%); }

  .brand { position: absolute; left: 28px; top: 24px; width: 160px; text-align: center; color: var(--white); }
  .brand__mark { display: block; width: 22px; height: 22px; border-radius: 50%; background: var(--white); margin: 0 auto 8px; }
  .brand__name { font-size: 7.5px; font-weight: 600; line-height: 1.35; letter-spacing: .3px; }

  .headline { position: absolute; left: 30px; top: 304px; width: 560px; text-transform: uppercase; font-weight: 400; font-size: 0; }
  .headline__line { display: block; white-space: nowrap; }
  .headline__line1 { font-size: 27px; line-height: 32px; height: 32px; color: var(--blue); }
  .headline__line2 { font-size: 17.5px; line-height: 24px; height: 24px; color: var(--green); }
  .headline__line3 { font-size: 22.5px; line-height: 30px; height: 30px; color: var(--green); }
  .headline strong { font-weight: 700; }
  .headline .hl-green { color: var(--green); }
  .headline .hl-blue { color: var(--blue); }

  .visit-band { position: absolute; left: 0; top: 405px; width: 596px; height: 48px;
    background: var(--band-blue); color: var(--white);
    font-size: 14.5px; font-weight: 600; line-height: 1.45; padding: 3px 34px 3px 30px; }

  .intro { position: absolute; left: 0; top: 453px; width: 383px; height: 157px; background: var(--light-grey); padding: 11px 22px 0 30px; }
  .intro__title { font-size: 13.5px; font-weight: 700; color: var(--green); text-transform: uppercase; line-height: 1.3; }
  .intro__tag { font-size: 9px; color: var(--blue); margin-top: 5px; }
  .intro__body { font-size: 9px; line-height: 1.5; margin-top: 1px; }

  .specialisms { position: absolute; left: 0; top: 610px; width: 383px; height: 232px; background: var(--white); }
  .specialisms__bar { background: var(--teal); color: var(--white); font-size: 10px; font-weight: 700;
    text-transform: uppercase; height: 22px; line-height: 22px; padding-left: 30px; }
  .specialisms__list { list-style: none; padding: 9px 60px 0 30px; }
  .specialisms__list li { position: relative; font-size: 9px; line-height: 1.45; padding-left: 28px; margin-bottom: 6.5px; }
  .tick { position: absolute; left: 0; top: 1px; width: 9px; height: 9px; }

  .contact { position: absolute; left: 383px; top: 453px; width: 213px; height: 389px; background: var(--column-green); }
  .contact__call { background: var(--dark); color: var(--white); text-align: center; height: 61px; padding-top: 10px; }
  .contact__label { font-family: "Roboto Condensed", sans-serif; font-weight: 700; font-size: 15.5px; letter-spacing: .2px; }
  .contact__phone { font-size: 16px; margin-top: 3px; }
  .contact__email { margin-top: 5px; background: var(--email-blue); color: var(--white); font-size: 9px; font-weight: 700;
    height: 22px; line-height: 22px; padding-left: 12px; }
  .contact__body { color: var(--white); font-size: 10px; line-height: 1.5; padding: 9px 13px 0 20px; }
  .registrations { position: absolute; left: 0; top: 290px; width: 213px; height: 82px;
    background: var(--white); display: flex; align-items: center; justify-content: space-around; padding: 0 10px; }
  .registrations__badge { width: 78px; height: 36px; border-radius: 4px; }
  .registrations__badge--hpva { background: #3aa7c9; }
  .registrations__badge--qelr { background: #7a4ea0; }
</style>
</head>
<body>
<div class="canvas">
  <article class="flyer">
    <div class="photo photo--fruit" role="img" aria-label="Basket of fresh fruit: apples, pears, grapes, oranges and strawberries"></div>
    <div class="photo photo--desserts" role="img" aria-label="Bowls of fruit sorbets and vanilla ice cream with raspberries"></div>
    <div class="photo photo--berries" role="img" aria-label="Glass of mixed berries"></div>
    <div class="photo photo--vegetables" role="img" aria-label="Fresh carrots, tomatoes and leafy greens"></div>

    <div class="brand">
      <span class="brand__mark"></span>
      <p class="brand__name">Brightpath Dietetics<br>&amp; Vitality Advisory</p>
    </div>

    <h1 class="headline">
      <span class="headline__line headline__line1">Do you <strong class="hl-green">experience low energy</strong>,</span>
      <span class="headline__line headline__line2">Low libido, <strong class="hl-blue">menstrual cycle complications</strong>,</span>
      <span class="headline__line headline__line3">or are you planning <strong>a baby?</strong></span>
    </h1>

    <p class="visit-band">Home visits available, at no extra cost within local area; I can visit your place of work or home.</p>

    <section class="intro">
      <h2 class="intro__title">Small changes to your diet may lead to big changes in your health.</h2>
      <p class="intro__tag">Eat well, live well.</p>
      <p class="intro__body">Discover exactly what YOU need to change and how to make these changes long lasting.<br>
      There is no 1 rule-fits-all. My nutritional advice aims to dig up the root cause to my client's health concerns. My lifestyle plans are completely personalised to an individual's needs and circumstances. I consider the whole person not just symptoms or disease.</p>
    </section>

    <section class="specialisms">
      <h3 class="specialisms__bar">Therapist &amp; wellness consultant, specialising in:</h3>
      <ul class="specialisms__list">
        <li><svg class="tick" viewBox="0 0 10 10"><rect x=".5" y=".5" width="9" height="9" fill="none" stroke="#1f8a3e"/><path d="M2.3 5.2l2 2 3.6-4.4" fill="none" stroke="#1f8a3e" stroke-width="1.4"/></svg>Fertility, IVF, pre-conception, pregnancy &amp; post-natal care</li>
        <li><svg class="tick" viewBox="0 0 10 10"><rect x=".5" y=".5" width="9" height="9" fill="none" stroke="#1f8a3e"/><path d="M2.3 5.2l2 2 3.6-4.4" fill="none" stroke="#1f8a3e" stroke-width="1.4"/></svg>Menstrual cycle challenges (PCOS, Endometriosis, PMS, heavy/irregular periods etc)</li>
        <li><svg class="tick" viewBox="0 0 10 10"><rect x=".5" y=".5" width="9" height="9" fill="none" stroke="#1f8a3e"/><path d="M2.3 5.2l2 2 3.6-4.4" fill="none" stroke="#1f8a3e" stroke-width="1.4"/></svg>Thyroid conditions</li>
        <li><svg class="tick" viewBox="0 0 10 10"><rect x=".5" y=".5" width="9" height="9" fill="none" stroke="#1f8a3e"/><path d="M2.3 5.2l2 2 3.6-4.4" fill="none" stroke="#1f8a3e" stroke-width="1.4"/></svg>Low libido</li>
        <li><svg class="tick" viewBox="0 0 10 10"><rect x=".5" y=".5" width="9" height="9" fill="none" stroke="#1f8a3e"/><path d="M2.3 5.2l2 2 3.6-4.4" fill="none" stroke="#1f8a3e" stroke-width="1.4"/></svg>Digestive health</li>
        <li><svg class="tick" viewBox="0 0 10 10"><rect x=".5" y=".5" width="9" height="9" fill="none" stroke="#1f8a3e"/><path d="M2.3 5.2l2 2 3.6-4.4" fill="none" stroke="#1f8a3e" stroke-width="1.4"/></svg>Chronic fatigue syndrome</li>
        <li><svg class="tick" viewBox="0 0 10 10"><rect x=".5" y=".5" width="9" height="9" fill="none" stroke="#1f8a3e"/><path d="M2.3 5.2l2 2 3.6-4.4" fill="none" stroke="#1f8a3e" stroke-width="1.4"/></svg>Perimenopause/menopause</li>
        <li><svg class="tick" viewBox="0 0 10 10"><rect x=".5" y=".5" width="9" height="9" fill="none" stroke="#1f8a3e"/><path d="M2.3 5.2l2 2 3.6-4.4" fill="none" stroke="#1f8a3e" stroke-width="1.4"/></svg>Weight management</li>
        <li><svg class="tick" viewBox="0 0 10 10"><rect x=".5" y=".5" width="9" height="9" fill="none" stroke="#1f8a3e"/><path d="M2.3 5.2l2 2 3.6-4.4" fill="none" stroke="#1f8a3e" stroke-width="1.4"/></svg>Type 2 diabetes, blood sugar dysregulation, high blood pressure, high cholesterol</li>
      </ul>
    </section>

    <aside class="contact">
      <div class="contact__call">
        <p class="contact__label">CALL MAEVE TODAY ON</p>
        <p class="contact__phone">085-4402-916</p>
      </div>
      <p class="contact__email">maeve@brightpathdietetics.ie</p>
      <div class="contact__body">
        <p>to book a consultation or for a free no obligation 15-minute mini consultation.</p>
        <p>Initial consultations typically last up to 2 hours, follow-ups 30 – 60 minutes. Further investigative tests may be recommended such as blood, urine, saliva sampling. These will always be agreed with the client in advance.</p>
      </div>
      <div class="registrations">
        <span class="registrations__badge registrations__badge--hpva" role="img" aria-label="HPVA registration badge"></span>
        <span class="registrations__badge registrations__badge--qelr" role="img" aria-label="QELR registration badge"></span>
      </div>
    </aside>
  </article>
</div>
</body>
</html>
```